Product Designer Business Card

Small product design, engineering and prototyping firm in need of a clean, professional business card design. To support our 3D design and drawing services, we offer 3D printing, molding, and casting of plastics, silicones, resins, etc. Our logo can still be modified/changed if necessary. The red/orange color is preferred, but may be substituted with blue or green, potentially. Either way, the colour of the logo should be match/compliment colors used throughout the design. One thought is to have the logo/contact info on one side, with the other side describing services offered, like with a small icon of 3D printer, molding, casting, and computer with a 3D model on-screen.
Industry/Entity Type
Mechanical Engineering
Contact Information for Business Card
Company: Kelvar Design
Phone: 613-582-9047
Email: mark@kelvardesign.ca

```html
<!DOCTYPE html>
<html lang="en">
<head>
<meta charset="utf-8">
<title>Kelvar Design – Business Card</title>
<link href="https://fonts.googleapis.com/css2?family=Montserrat:wght@400;600&family=Roboto:wght@300;400;500&display=swap" rel="stylesheet">
<style>
  :root {
    --bg: #2c2c2c;
    --brand-red: #e0220c;
    --brand-dark: #7a1a10;
    --paper: #ffffff;
    --ink-grey: #6b6b6b;
    --icon-fill: rgba(255, 255, 255, 0.28);
  }
  html, body {
    margin: 0;
    width: 1200px;
    height: 896px;
    overflow: hidden;
    background: var(--bg);
  }
  .stage {
    width: 1200px;
    height: 896px;
    display: flex;
    align-items: center;
    justify-content: center;
    gap: 40px;
  }
  .card {
    position: relative;
    width: 520px;
    height: 300px;
    border-radius: 22px;
    overflow: hidden;
    box-shadow: 0 10px 30px rgba(0, 0, 0, 0.45);
  }
  .card--front { background: var(--brand-red); }
  .card--back  { background: var(--paper); }

  .wordmark {
    position: absolute;
    display: flex;
    align-items: center;
    gap: 12px;
    font-family: "Montserrat", sans-serif;
    font-weight: 600;
    letter-spacing: 0.06em;
  }
  .wordmark__dot {
    border-radius: 50%;
    flex: none;
  }
  .card--front .wordmark { left: 48px; top: 128px; font-size: 36px; color: var(--paper); }
  .card--front .wordmark__dot { width: 30px; height: 30px; background: var(--paper); }
  .card--back .wordmark { left: 40px; top: 44px; font-size: 30px; color: var(--brand-dark); }
  .card--back .wordmark__dot { width: 26px; height: 26px; background: var(--brand-red); }

  .services {
    position: absolute;
    right: 28px;
    top: 22px;
    display: flex;
    flex-direction: column;
    gap: 16px;
  }
  .service {
    display: flex;
    flex-direction: column;
    align-items: center;
    gap: 4px;
    font-family: "Roboto", sans-serif;
    font-size: 11px;
    color: var(--paper);
  }
  .service__icon {
    width: 56px;
    height: 50px;
    border-radius: 6px;
    background: var(--icon-fill);
  }

  .contact-rule {
    position: absolute;
    left: 0;
    right: 36px;
    top: 208px;
    height: 1px;
    background: var(--brand-red);
  }
  .contact-tab {
    position: absolute;
    left: 0;
    top: 200px;
    width: 8px;
    height: 18px;
    background: var(--brand-red);
  }
  .person {
    position: absolute;
    left: 40px;
    top: 146px;
    font-family: "Roboto", sans-serif;
  }
  .person__name {
    margin: 0;
    font-size: 22px;
    font-weight: 500;
    letter-spacing: 0.02em;
    text-transform: uppercase;
    color: var(--brand-red);
  }
  .person__title {
    margin: 2px 0 0;
    font-size: 14px;
    font-weight: 300;
    color: var(--ink-grey);
  }
  .contact-list {
    position: absolute;
    left: 40px;
    top: 222px;
    margin: 0;
    padding: 0;
    list-style: none;
    font-family: "Roboto", sans-serif;
    font-size: 15px;
    font-weight: 300;
    color: var(--ink-grey);
  }
  .contact-list li {
    display: flex;
    align-items: center;
    gap: 8px;
    margin-bottom: 6px;
  }
  .contact-list svg { width: 12px; height: 12px; fill: var(--brand-red); }
</style>
</head>
<body>
<main class="stage">
  <section class="card card--front" aria-label="Card front">
    <div class="wordmark"><span class="wordmark__dot"></span>Kelvar Design</div>
    <ul class="services" style="margin:0;padding:0;list-style:none;">
      <li class="service"><div class="service__icon" role="img" aria-label="Molding machine icon"></div>Molding</li>
      <li class="service"><div class="service__icon" role="img" aria-label="3D printer icon"></div>3D printer</li>
      <li class="service"><div class="service__icon" role="img" aria-label="Casting icon"></div>Casting</li>
    </ul>
  </section>

  <section class="card card--back" aria-label="Card back">
    <div class="wordmark"><span class="wordmark__dot"></span>Kelvar Design</div>
    <div class="person">
      <p class="person__name">Tomas Reyna</p>
      <p class="person__title">President</p>
    </div>
    <div class="contact-rule"></div>
    <div class="contact-tab"></div>
    <ul class="contact-list">
      <li>
        <svg viewBox="0 0 24 24" aria-hidden="true"><path d="M6.6 10.8a15 15 0 0 0 6.6 6.6l2.2-2.2a1 1 0 0 1 1-.25 11.4 11.4 0 0 0 3.6.57 1 1 0 0 1 1 1V20a1 1 0 0 1-1 1A17 17 0 0 1 3 4a1 1 0 0 1 1-1h3.5a1 1 0 0 1 1 1c0 1.25.2 2.45.57 3.57a1 1 0 0 1-.25 1z"/></svg>
        613-582-9047
      </li>
      <li>
        <svg viewBox="0 0 24 24" aria-hidden="true"><path d="M2 5h20v14H2z M4 7v.5l8 5 8-5V7l-8 5z" fill-rule="evenodd"/></svg>
        mark@kelvardesign.ca
      </li>
    </ul>
  </section>
</main>
</body>
</html>
```